Storm Restoration Contractor needs a professional letterhead design

Looking for a professional letterhead design. Not looking for your cheapo MS Word standard ones that are readily available. Dont want it to be cookie cutter look like ones readily available online. We just recently changed our logo and want to freshen up all our documents. Our company handles restoring a property back to a pre-loss condition after a storm damages it. For example, wind, hail, flood, fire losses.

Target Market(s)

Property Owners, Homeowners, Property Owners, Commercial Property Owners, Property Management Companies

Industry/Entity Type

Construction Company

Requirements
Must have
• Professional, Use 1 of 2 logo options
• Storm Restoration, Roofing, Siding, Windows

```html
<!DOCTYPE html>
<html lang="en">
<head>
<meta charset="utf-8">
<title>Stormline Exteriors Letterhead</title>
<link href="https://fonts.googleapis.com/css2?family=Open+Sans:wght@400;600;700&display=swap" rel="stylesheet">
<style>
  :root {
    --backdrop: #e9e9e9;
    --paper: #ffffff;
    --brand-blue: #1f73c0;
    --brand-grey: #4a4a4a;
    --text: #5a5a5a;
    --heading: #333333;
    --signature-fill: #ececec;
  }
  * { box-sizing: border-box; margin: 0; padding: 0; }
  html, body {
    width: 1200px; height: 795px; overflow: hidden;
    background: var(--backdrop);
    font-family: "Open Sans", Arial, sans-serif;
  }
  .letterhead {
    position: absolute; left: 330px; top: 28px;
    width: 540px; height: 740px;
    background: var(--paper);
    box-shadow: 0 6px 20px rgba(0,0,0,0.12);
    overflow: hidden;
  }
  .brand {
    position: absolute; left: 42px; top: 46px;
    display: flex; align-items: center; gap: 8px;
  }
  .brand-dot {
    width: 26px; height: 26px; border-radius: 50%;
    background: var(--brand-blue);
  }
  .brand-name {
    font-size: 13px; font-weight: 600; letter-spacing: 1.5px;
    color: var(--brand-blue); text-transform: uppercase;
  }
  .contact {
    position: absolute; right: 40px; top: 40px;
    text-align: right; font-size: 7.5px; line-height: 1.55;
    font-style: normal; color: var(--heading);
  }
  .contact-line { display: flex; justify-content: flex-end; align-items: center; gap: 4px; }
  .contact-icon { width: 8px; height: 8px; }
  .letter {
    position: absolute; left: 42px; top: 130px; width: 440px;
    color: var(--text); font-size: 9px; line-height: 1.5;
  }
  .salutation {
    font-size: 11px; font-weight: 700; color: var(--heading);
    margin-bottom: 8px;
  }
  .letter p { margin-bottom: 10px; }
  .signature {
    position: absolute; left: 42px; top: 400px;
    width: 110px; height: 40px; background: var(--signature-fill);
    border-radius: 3px;
  }
  .footer-wave { position: absolute; left: 0; bottom: 0; width: 540px; height: 740px; }
  .website {
    position: absolute; left: 44px; bottom: 16px;
    color: #ffffff; font-size: 11px; letter-spacing: 0.5px;
  }
</style>
</head>
<body>
  <main class="letterhead">
    <header class="brand">
      <span class="brand-dot"></span>
      <span class="brand-name">Stormline Exteriors</span>
    </header>

    <address class="contact">
      <div>2280 Harbor Lane</div>
      <div>Fairview, CA 90210</div>
      <div class="contact-line">(555) 014-2286
        <svg class="contact-icon" viewBox="0 0 10 10"><circle cx="5" cy="5" r="5" fill="var(--brand-blue)"/><path d="M3.2 2.6l1 1-.5.7a3.5 3.5 0 0 0 2 2l.7-.5 1 1-.6.8c-2.2-.2-4.2-2.2-4.4-4.4z" fill="#fff"/></svg>
      </div>
      <div class="contact-line">(555) 014-2287
        <svg class="contact-icon" viewBox="0 0 10 10"><circle cx="5" cy="5" r="5" fill="var(--brand-blue)"/><path d="M3.2 2.6l1 1-.5.7a3.5 3.5 0 0 0 2 2l.7-.5 1 1-.6.8c-2.2-.2-4.2-2.2-4.4-4.4z" fill="#fff"/></svg>
      </div>
      <div>info@stormlineexteriors.com</div>
    </address>

    <section class="letter">
      <div class="salutation">Dear Mr. John,</div>
      <p>Lorem Ipsum is simply dummy text of the printing and typesetting industry. Lorem Ipsum has been the industry's standard dummy text ever since the 1500s, when an unknown printer took a galley of type and scrambled it to make a type specimen book. It has survived not only five centuries, but also the leap into electronic typesetting, remaining essentially unchanged.</p>
      <p>The standard chunk of Lorem Ipsum used since the 1500s is reproduced below for those interested. Sections 1.10.32 and 1.10.33 from the classic treatise on ethics are also reproduced in their exact original form, accompanied by English versions from a later translation of the same work.</p>
      <p>Lorem Ipsum is simply dummy text of the printing and typesetting industry. Lorem Ipsum has been the industry's standard dummy text ever since the 1500s, when an unknown printer took a galley of type and scrambled it to make a type specimen book. It has survived not only five centuries, but also the leap into electronic typesetting, remaining essentially unchanged. It was popularised in the</p>
    </section>

    <div class="signature" role="img" aria-label="Handwritten signature of the sender"></div>

    <svg class="footer-wave" viewBox="0 0 540 740" aria-hidden="true">
      <path d="M0,694 C190,684 390,630 540,498 L540,514 C390,648 190,700 0,707 Z" fill="var(--brand-grey)"/>
      <path d="M0,712 C200,706 400,652 540,524 L540,740 L0,740 Z" fill="var(--brand-blue)"/>
    </svg>
    <div class="website">www.stormlineexteriors.com</div>
  </main>
</body>
</html>
```